New Business Card Design

We would like to refresh our business cards and make them look better. We are an IT company specialising in Cloud Services, IT Managed Services, software and hardware. I have attached a PSD of our current design. Also attached our logo.
Updates

I have uploaded all new logos in EPS format.

Can you please edit all designs to include a job title for Marcus Hollis, eg. General Manager

Industry/Entity Type

Software

Colors
ffffff

Requirements
Must have
• Please use white background.
Should not have
• Black background

```html
<!DOCTYPE html>
<html lang="en">
<head>
<meta charset="utf-8">
<title>Meridian Systems – Business Cards</title>
<link rel="stylesheet" href="https://fonts.googleapis.com/css2?family=Open+Sans:wght@400;600&display=swap">
<style>
  :root {
    --page: #e9e6e1;
    --card: #ffffff;
    --ink: #2b2b2b;
    --muted: #555a60;
    --accent: #c23a26;
    --edge: #d9d9d9;
  }
  * { box-sizing: border-box; margin: 0; padding: 0; }
  html, body { width: 1200px; height: 720px; overflow: hidden; }
  body {
    background: var(--page);
    font-family: "Open Sans", Arial, sans-serif;
    color: var(--ink);
    display: flex;
    align-items: center;
    justify-content: center;
    gap: 40px;
  }
  .card {
    position: relative;
    width: 520px;
    height: 297px;
    background: var(--card);
    border: 1px solid var(--edge);
    box-shadow: 0 6px 18px rgba(0,0,0,0.12);
    overflow: hidden;
  }

  /* Company name */
  .brand {
    display: flex;
    align-items: center;
    gap: 10px;
  }
  .brand-name {
    font-weight: 400;
    color: var(--ink);
    line-height: 1.1;
    letter-spacing: 0;
    white-space: nowrap;
  }
  .brand-square {
    flex: none;
    background: var(--ink);
  }

  /* Front card */
  .card-front .brand { position: absolute; left: 34px; top: 44px; }
  .card-front .brand-name { font-size: 24px; }
  .card-front .brand-square { width: 12px; height: 12px; }

  .person { position: absolute; left: 34px; top: 126px; }
  .person-name { font-size: 15px; font-weight: 600; color: var(--accent); line-height: 1.2; }
  .person-title { font-size: 12px; color: var(--ink); }

  .contact-list {
    position: absolute;
    left: 34px;
    top: 176px;
    list-style: none;
    font-size: 12px;
    color: var(--muted);
  }
  .contact-list li {
    display: flex;
    align-items: center;
    gap: 9px;
    height: 22px;
  }
  .contact-icon { width: 13px; height: 13px; flex: none; }

  /* Back card */
  .card-back .brand {
    position: absolute;
    left: 40px; right: 40px;
    top: 86px;
    justify-content: center;
  }
  .card-back .brand-name { font-size: 28px; }
  .card-back .brand-square { width: 14px; height: 14px; }

  .tagline {
    position: absolute;
    left: 40px; right: 40px;
    bottom: 48px;
    text-align: center;
    font-size: 16px;
    line-height: 1.45;
    color: var(--muted);
  }
</style>
</head>
<body>

  <section class="card card-front" aria-label="Business card front">
    <div class="brand">
      <span class="brand-square"></span>
      <span class="brand-name">Meridian Systems</span>
    </div>

    <div class="person">
      <p class="person-name">Marcus Hollis</p>
      <p class="person-title">General Manager</p>
    </div>

    <ul class="contact-list">
      <li>
        <svg class="contact-icon" viewBox="0 0 16 16" aria-hidden="true">
          <circle cx="8" cy="8" r="8" fill="var(--accent)"/>
          <path d="M5.2 4.2l1.5-.4.9 2-1 .8a5 5 0 0 0 2.8 2.8l.8-1 2 .9-.4 1.5c-3.6.2-6.8-3-6.6-6.6z" fill="#fff"/>
        </svg>
        07 4815 6200
      </li>
      <li>
        <svg class="contact-icon" viewBox="0 0 16 16" aria-hidden="true">
          <circle cx="8" cy="8" r="8" fill="var(--accent)"/>
          <rect x="5.5" y="3.5" width="5" height="9" rx="1" fill="#fff"/>
          <rect x="6.4" y="4.6" width="3.2" height="5.6" fill="var(--accent)"/>
        </svg>
        0412 557 309
      </li>
      <li>
        <svg class="contact-icon" viewBox="0 0 16 16" aria-hidden="true">
          <circle cx="8" cy="8" r="8" fill="var(--accent)"/>
          <rect x="4" y="5" width="8" height="6" fill="#fff"/>
          <path d="M4 5l4 3.3L12 5" fill="none" stroke="var(--accent)" stroke-width="1"/>
        </svg>
        mhollis@meridiansys.com.au
      </li>
      <li>
        <svg class="contact-icon" viewBox="0 0 16 16" aria-hidden="true">
          <circle cx="8" cy="8" r="8" fill="var(--accent)"/>
          <circle cx="8" cy="8" r="4.3" fill="none" stroke="#fff" stroke-width="1"/>
          <ellipse cx="8" cy="8" rx="1.8" ry="4.3" fill="none" stroke="#fff" stroke-width="1"/>
          <line x1="3.7" y1="8" x2="12.3" y2="8" stroke="#fff" stroke-width="1"/>
        </svg>
        www.meridiansys.com.au
      </li>
    </ul>
  </section>

  <section class="card card-back" aria-label="Business card back">
    <div class="brand">
      <span class="brand-square"></span>
      <span class="brand-name">Meridian Systems</span>
    </div>
    <p class="tagline">
      We are an IT company specializing in Cloud Services<br>
      IT Managed Services, software and hardware
    </p>
  </section>

</body>
</html>
```